BOLD & MINIMALIST DESIGN NEEDED

We want a very bold but minimalistic business card design that is impactful and utilizes both sides of the business card. Our current logo is included for your use.

We want bold fonts and good use of negative space. We don't want the logo to overpower the design.

Target Market(s)

Professionals who are building new commercial buildings.

Industry/Entity Type

Construction

Contact Information for Business Card

Name, Title, email, office phone, cell phone, website

Font styles to use
Serif
Sans Serif

Requirements
Must have
• Bold design!

```html
<!DOCTYPE html>
<html lang="en">
<head>
<meta charset="utf-8">
<title>Stonereach Build Co – Business Card</title>
<link rel="stylesheet" href="https://fonts.googleapis.com/css2?family=Montserrat:wght@600&family=Roboto:wght@500;700;900&display=swap">
<style>
  :root {
    --backdrop: #dfe4e2;
    --card: #ffffff;
    --ink: #1a1a1a;
    --text-grey: #555555;
    --accent: #7cc242;
    --rule: #222222;
  }
  * { box-sizing: border-box; margin: 0; padding: 0; }
  html, body {
    width: 1200px;
    height: 716px;
    overflow: hidden;
    background: var(--backdrop);
  }
  .canvas {
    position: relative;
    width: 1200px;
    height: 716px;
  }
  .card {
    position: absolute;
    left: 369px;
    width: 461px;
    height: 264px;
    background: var(--card);
    border-radius: 12px;
    box-shadow: 0 2px 6px rgba(0,0,0,0.08);
  }
  .card--front { top: 94px; }
  .card--back { top: 382px; }

  .brand {
    display: flex;
    align-items: center;
    gap: 10px;
    font-family: "Roboto", sans-serif;
    font-weight: 900;
    color: var(--ink);
    text-transform: uppercase;
    letter-spacing: 0.5px;
  }
  .brand__square {
    background: var(--accent);
    flex: none;
  }
  .card--front .brand {
    position: absolute;
    left: 0; right: 0;
    top: 104px;
    justify-content: center;
    font-size: 34px;
    line-height: 1;
  }
  .card--front .brand__square { width: 26px; height: 26px; }

  .card--back .brand {
    position: absolute;
    right: 22px;
    top: 52px;
    font-size: 17px;
    line-height: 1;
    gap: 6px;
  }
  .card--back .brand__square { width: 13px; height: 13px; }

  .person {
    position: absolute;
    left: 17px;
    top: 144px;
    color: var(--text-grey);
  }
  .person__name {
    font-family: "Montserrat", sans-serif;
    font-weight: 600;
    font-size: 15.5px;
    line-height: 18px;
  }
  .person__title {
    font-family: "Montserrat", sans-serif;
    font-weight: 600;
    font-size: 11.5px;
    line-height: 16px;
    margin-top: 2px;
  }

  .address, .contacts {
    position: absolute;
    right: 20px;
    text-align: right;
    font-family: "Roboto", sans-serif;
    font-weight: 700;
    font-size: 12.5px;
    line-height: 16.5px;
    color: var(--text-grey);
  }
  .address { top: 145px; }
  .contacts { top: 191px; }

  .divider {
    position: absolute;
    left: 17px;
    top: 185px;
    width: 424px;
    height: 1.5px;
    background: var(--rule);
  }
</style>
</head>
<body>
<main class="canvas">
  <section class="card card--front" aria-label="Card front">
    <div class="brand">
      <span class="brand__square"></span>
      <span class="brand__name">Stonereach</span>
    </div>
  </section>

  <section class="card card--back" aria-label="Card back">
    <div class="brand">
      <span class="brand__square"></span>
      <span class="brand__name">Stonereach</span>
    </div>

    <div class="person">
      <p class="person__name">MIRELA DANCOTT</p>
      <p class="person__title">Designer</p>
    </div>

    <div class="address">
      <p>Your Address Here</p>
      <p>R. No. 05 P.O. 5400, BD</p>
    </div>

    <div class="divider"></div>

    <div class="contacts">
      <p>+123-45-67890</p>
      <p>info@youremail.com</p>
      <p>www.infoweibsite.com</p>
    </div>
  </section>
</main>
</body>
</html>
```